Design a Book Cover for Veltrix Development Book

I need to create an eBook design for a technical book with the following info.
Title: Brisko Veltrix - Grow Into A Veltrix Builder in 90 Sprints!
Subtitle: Learn how to Build 10 Complete Veltrix Apps with Marzel.
Author: Teo Brannick
Delivery should include all book cover formats, 2D, 3D, Kindle, Print, etc.
Target Market(s)
People who want to learn Veltrix development, people who want to switch careers to programming.
Industry/Entity Type
Programming
Colors
fec214
0792cd
ec1f27
Requirements
Should not have
- Do not use Veltrix logo (green robot), Do not use Marzel logo (K).

```html
<!DOCTYPE html>
<html lang="en">
<head>
<meta charset="utf-8">
<title>Brisko Veltrix – Book Cover</title>
<link rel="stylesheet" href="https://fonts.googleapis.com/css2?family=Montserrat:wght@500;700&family=Playfair+Display:wght@700;800&display=swap">
<style>
  :root {
    --page-bg: #e3e3e3;
    --cover-bg: #3b3b3b;
    --accent-yellow: #c4a404;
    --text-white: #ececec;
    --text-grey: #a9a9a9;
  }
  html, body {
    margin: 0;
    padding: 0;
    width: 1200px;
    height: 1200px;
    overflow: hidden;
    background: var(--page-bg);
  }
  .book-cover {
    position: absolute;
    left: 250px;
    top: 40px;
    width: 700px;
    height: 1120px;
    background: var(--cover-bg);
  }
  .title-block {
    position: absolute;
    left: 0;
    top: 0;
    width: 700px;
    height: 720px;
  }
  .title-word {
    font-family: "Playfair Display", Georgia, serif;
    font-weight: 800;
    font-size: 124px;
    fill: var(--cover-bg);
  }
  .tagline {
    position: absolute;
    left: 0;
    width: 670px;
    top: 742px;
    margin: 0;
    text-align: center;
    font-family: "Montserrat", Arial, sans-serif;
    font-weight: 500;
    font-size: 24px;
    line-height: 32px;
    letter-spacing: 0.5px;
    text-transform: uppercase;
    color: var(--accent-yellow);
  }
  .tagline strong { font-weight: 700; }
  .subtitle {
    position: absolute;
    left: 170px;
    width: 334px;
    top: 838px;
    margin: 0;
    padding: 7px 0 8px;
    border-top: 1px dotted var(--accent-yellow);
    border-bottom: 1px dotted var(--accent-yellow);
    text-align: center;
    font-family: "Montserrat", Arial, sans-serif;
    font-weight: 500;
    font-size: 14px;
    line-height: 17px;
    letter-spacing: 0.3px;
    text-transform: uppercase;
    color: var(--text-grey);
  }
  .author {
    position: absolute;
    left: 0;
    width: 670px;
    top: 990px;
    margin: 0;
    text-align: center;
    font-family: "Playfair Display", Georgia, serif;
    font-weight: 700;
    font-size: 66px;
    line-height: 80px;
    letter-spacing: 1px;
    text-transform: uppercase;
    white-space: nowrap;
  }
  .author-first { color: var(--text-white); }
  .author-last { color: var(--accent-yellow); }
</style>
</head>
<body>
  <main class="book-cover">
    <svg class="title-block" viewBox="0 0 700 720" width="700" height="720" aria-label="Brisko Veltrix">
      <rect class="title-panel" x="63" y="136" width="534" height="551" rx="14" fill="var(--accent-yellow)"/>
      <rect class="title-notch" x="60" y="462" width="22" height="76" fill="var(--cover-bg)"/>
      <rect class="title-notch" x="60" y="578" width="22" height="70" fill="var(--cover-bg)"/>
      <text class="title-word" x="84" y="526" textLength="425" lengthAdjust="spacingAndGlyphs">brisko</text>
      <text class="title-word" x="84" y="641" textLength="494" lengthAdjust="spacingAndGlyphs">veltrix</text>
    </svg>

    <p class="tagline">Grow into a<br>Veltrix builder<br>in <strong>90 Sprints!</strong></p>

    <p class="subtitle">Learn how to build 10 complete<br>Veltrix apps with Marzel.</p>

    <h2 class="author"><span class="author-first">Teo</span> <span class="author-last">Brannick</span></h2>
  </main>
</body>
</html>
```